Bright Harbor Web Design & Marketing

Will award a 2nd place prize of $100.00 if someone can come up with a logo to match this design!
Updates

Okay, I'm really looking to see some better designs here. What do you think will bring the best designs out? Please remember with all future submissions I'm looking for a cartoon style / illustrator style website. I'm not sure what the technical term is for it, so I uploaded some images in the brief.

Target Market(s)

Small Business Owners

Industry/Entity Type

Marketing

Logo Text

BrightHarbor.com

Number of Pages Required

1 page

Colors

Designer to choose colors to be used in the design.

Requirements
Must have
• Logo should say BrightHarbor.com I would like more than just a text logo. I want some sort of cool custom graphic / icon with it that will look nice on shirts/hats/etc

```html
<!DOCTYPE html>
<html lang="en">
<head>
<meta charset="utf-8">
<title>Bright Harbor Web Design &amp; Marketing</title>
<link rel="stylesheet" href="https://fonts.googleapis.com/css2?family=Cinzel:wght@600;700&family=Open+Sans:wght@400;600;700&family=Tinos:wght@400;700&display=swap">
<style>
:root{
  --blue:#1b6fb8;
  --blue-dark:#124f86;
  --orange:#f08a1c;
  --ink:#222831;
  --text:#555b63;
  --muted:#8a9099;
  --dark:#1e2a30;
  --cream:#f6f3ea;
  --sky:#dce9f5;
  --white:#ffffff;
  --line:#d9dde2;
}
*{box-sizing:border-box;margin:0;padding:0}
html,body{width:1200px;height:4455px;overflow:hidden}
body{font-family:"Open Sans",Arial,sans-serif;color:var(--text);background:var(--white);position:relative}
.section{position:absolute;left:0;width:1200px}
.heading{font-family:"Cinzel",Georgia,serif;font-weight:700;color:var(--ink);text-align:center;letter-spacing:2px;font-size:31px}
.lead{font-family:"Tinos",Georgia,serif;font-size:14px;line-height:20px;text-align:center;color:var(--text);width:980px;margin:0 auto}
.btn{display:inline-block;font-family:"Open Sans",Arial,sans-serif;color:var(--white);border-radius:3px}

/* header */
.site-header{top:0;height:89px;background:var(--white)}
.brand{position:absolute;left:148px;top:16px;display:flex;align-items:center;gap:10px}
.brand-dot{width:46px;height:46px;border-radius:50%;background:var(--blue)}
.brand-name{font-family:"Tinos",Georgia,serif;font-weight:700;font-size:36px;color:var(--blue)}
.phone{position:absolute;right:150px;top:28px;display:flex;align-items:center;gap:8px;font-size:26px;color:var(--blue-dark);font-weight:600}
.main-nav{top:89px;height:30px;background:var(--blue)}
.main-nav ul{list-style:none;display:flex;position:absolute;left:140px}
.main-nav li{height:30px;line-height:30px;font-family:"Cinzel",Georgia,serif;font-size:14px;color:var(--white);width:182px;text-align:center;letter-spacing:1px}
.main-nav li.active{background:var(--orange);width:110px}

/* hero */
.hero{top:119px;height:475px;overflow:hidden;
  background:
    radial-gradient(ellipse 300px 140px at 330px 400px,rgba(255,190,90,.45),transparent 70%),
    radial-gradient(ellipse 380px 160px at 720px 420px,rgba(255,170,70,.35),transparent 70%),
    radial-gradient(ellipse 260px 120px at 1040px 410px,rgba(120,180,255,.35),transparent 70%),
    radial-gradient(ellipse 500px 200px at 600px 480px,rgba(40,60,90,.9),transparent 80%),
    linear-gradient(180deg,#0c1a3a 0%,#183566 40%,#2f4a78 62%,#2b3448 80%,#141922 100%)}
.hero-title{position:absolute;right:140px;top:112px;width:380px;text-align:right;color:var(--white);font-size:25px;line-height:34px;font-weight:400;text-shadow:0 1px 3px rgba(0,0,0,.5)}
.hero-cta{position:absolute;right:140px;top:238px;background:var(--blue);font-size:22px;padding:6px 16px;display:flex;gap:8px;align-items:center}
.hero-arrow{position:absolute;top:232px;width:22px;height:32px;background:rgba(255,255,255,.8);color:var(--ink);text-align:center;line-height:32px;font-size:16px}

/* about */
.about{top:594px;height:638px}
.about .heading{margin-top:60px}
.about .heading span{color:var(--orange);font-family:"Tinos",Georgia,serif}
.about .lead{margin-top:16px}
.video-frame{position:absolute;left:345px;top:200px;width:510px;height:326px;border-radius:12px;background:linear-gradient(180deg,#3a3a3a,#1f1f1f)}
.video-screen{position:absolute;left:16px;top:16px;width:478px;height:278px;background:linear-gradient(180deg,#f1f1f1,#d6d6d6)}
.video-title{position:absolute;left:44px;top:118px;display:flex;align-items:center;gap:10px;font-family:"Open Sans",Arial,sans-serif;font-weight:700;font-size:30px;color:var(--orange)}
.video-title i{width:34px;height:34px;border-radius:50%;background:#3a4654;display:inline-block}
.video-stand{position:absolute;left:325px;top:526px;width:550px;height:10px;border-radius:0 0 6px 6px;background:linear-gradient(180deg,#cfd3d6,#9aa0a5)}
.about-cta{position:absolute;left:483px;top:552px;background:#5b5b5b;font-size:22px;padding:6px 20px;display:flex;gap:8px;align-items:center}

/* services */
.services{top:1232px;height:758px;background:
  radial-gradient(ellipse 420px 260px at 160px 620px,rgba(120,80,40,.35),transparent 70%),
  radial-gradient(ellipse 420px 260px at 1060px 620px,rgba(140,90,40,.35),transparent 70%),
  linear-gradient(180deg,#1e2b31 0%,#24343a 50%,#2c2a26 100%)}
.services .heading{color:var(--white);margin-top:40px}
.services .lead{color:#cfd5d8;margin-top:10px}
.services-art{position:absolute;left:0;top:0}

/* plans */
.plans{top:1990px;height:668px;background:var(--white)}
.plans .heading{margin-top:52px}
.plans-floor{position:absolute;left:0;top:430px;width:1200px;height:238px;background:linear-gradient(180deg,#e4e1dc 0%,#cfa06a 18%,#b67f45 60%,#9c6a36 100%)}
.plan{position:absolute;top:142px;width:210px;height:486px;background:var(--white);border-top:3px solid var(--blue);box-shadow:0 2px 8px rgba(0,0,0,.25);text-align:center}
.plan.raised{top:124px}
.plan-icon{width:58px;height:58px;border-radius:50%;background:#eef3f8;border:2px solid var(--line);margin:30px auto 0;display:flex;align-items:center;justify-content:center}
.plan-name{font-size:15px;color:var(--ink);font-weight:600;margin-top:18px}
.plan-body{background:#faf8f6;margin-top:14px;padding-top:18px;height:346px}
.plan-from{font-family:"Tinos",Georgia,serif;font-size:12px;color:var(--muted)}
.plan-price{font-family:"Tinos",Georgia,serif;font-size:34px;color:var(--ink);line-height:40px}
.plan-price sup{font-size:16px}
.plan-price small{font-size:14px}
.plan-price.accent{color:var(--orange)}
.plan-list{list-style:none;text-align:left;margin:24px 0 0 30px;font-size:11px;line-height:28px;color:var(--text);white-space:nowrap}
.plan-list li::before{content:"›";margin-right:8px;color:var(--muted)}
.plan-btn{background:#555;font-size:12px;padding:6px 18px;margin-top:24px}
.plan-btn.accent{background:var(--orange)}
.plan-more{font-size:11px;color:var(--ink);margin-top:6px}

/* clients */
.clients{top:2658px;height:267px;background:var(--cream)}
.clients .heading{margin-top:48px}
.clients .lead{margin-top:10px}
.client-row{position:absolute;left:144px;top:170px;display:flex;gap:16px}
.client{width:100px;height:40px;background:var(--white);display:flex;align-items:center;justify-content:center;gap:5px;font-size:13px;font-weight:700;color:#333}
.client i{width:9px;height:9px;background:#333;border-radius:50%;display:inline-block}
.row-arrow{position:absolute;top:178px;font-size:24px;color:#999}

/* why */
.why{top:2925px;height:535px;background:var(--sky)}
.why .heading{margin-top:45px}
.why .lead{margin-top:10px}
.why-art{position:absolute;left:0;top:0}

/* team */
.team{top:3460px;height:312px}
.team .heading{margin-top:30px}
.team .lead{margin-top:12px}
.member{position:absolute;top:150px;width:410px;height:146px;border:1px solid var(--line);background:var(--white)}
.member-photo{position:absolute;left:12px;top:-2px;width:70px;height:70px;background:linear-gradient(180deg,#d9dcdf,#7d8489)}
.member-name{position:absolute;left:96px;top:14px;font-size:13px;font-weight:700;color:var(--ink)}
.member-role{position:absolute;left:96px;top:32px;font-size:12px;color:var(--blue)}
.member-bio{position:absolute;left:12px;top:84px;width:380px;font-size:11px;line-height:16px;color:var(--text)}

/* inquiry */
.inquiry{top:3772px;height:386px;background:var(--white)}
.inquiry-photo{position:absolute;left:0;top:10px;width:450px;height:376px;background:
  radial-gradient(ellipse 120px 90px at 300px 300px,rgba(255,255,255,.9),transparent 70%),
  radial-gradient(ellipse 200px 140px at 330px 170px,rgba(90,100,110,.55),transparent 70%),
  radial-gradient(ellipse 160px 90px at 120px 250px,rgba(225,190,165,.6),transparent 70%),
  linear-gradient(135deg,#fafafa,#e6e9ec 55%,#c9cfd4)}
.inquiry .heading{position:absolute;left:490px;top:50px;width:535px;text-align:left}
.field{position:absolute;font-size:11px;color:var(--text);border-bottom:1px solid var(--line);height:28px;padding-top:6px;width:260px}
.field.box{border:1px solid var(--line);padding-left:8px;height:74px;width:535px}
.submit{position:absolute;left:490px;top:334px;background:var(--blue);font-size:12px;padding:5px 14px}

/* footer */
.site-footer{top:4158px;height:267px;background:
  radial-gradient(ellipse 600px 120px at 600px 260px,rgba(110,120,130,.35),transparent 70%),
  linear-gradient(180deg,#25323a,#1a232a)}
.foot-col{position:absolute;top:38px;color:#d9dee2;font-size:11px;line-height:19px}
.foot-col h4{font-family:"Tinos",Georgia,serif;font-size:16px;color:var(--white);font-weight:400;margin-bottom:8px}
.foot-col h4 span{color:var(--orange)}
.foot-col ul{list-style:disc;padding-left:14px}
.foot-input{width:214px;height:24px;background:var(--white);margin-top:14px;color:#666;padding:4px 6px}
.foot-btn{background:var(--blue);padding:3px 10px;margin-top:8px;font-size:12px}
.foot-mark{position:absolute;left:860px;top:40px;width:120px;height:120px;border-radius:50%;background:rgba(255,255,255,.12)}
.copyright{top:4425px;height:30px;background:#0f161b;color:#b9c0c5;font-size:11px;line-height:30px}
</style>
</head>
<body>

<header class="section site-header">
  <div class="brand"><span class="brand-dot"></span><span class="brand-name">BrightHarbor.com</span></div>
  <div class="phone">
    <svg width="28" height="28" viewBox="0 0 28 28"><circle cx="14" cy="14" r="12.5" fill="none" stroke="#124f86" stroke-width="2"/><path d="M9 8c1-1 2-1 3 0l1.5 2.5c.5 1 0 1.8-.8 2.3 .8 1.8 2 3 3.8 3.8.5-.8 1.3-1.3 2.3-.8L21.3 17c1 1 1 2 0 3-2 2-5 1-8-2s-4-6-4.3-10z" fill="#124f86"/></svg>
    555-014-2290
  </div>
</header>

<nav class="section main-nav">
  <ul>
    <li class="active">HOME</li><li>SERVICES &amp; PRICING</li><li>OUR TEAM</li><li>CLIENTS</li><li>CONTACT US</li>
  </ul>
</nav>

<section class="section hero" role="img" aria-label="Night skyline of a city with a tall observation tower">
  <p class="hero-title">The Design &amp; Marketing Team That Always Puts Honesty &amp; Loyalty Before Profits</p>
  <span class="btn hero-cta">
    <svg width="20" height="20" viewBox="0 0 20 20"><path d="M4 3c1-1 2-1 3 0l2 3c.5 1 0 2-1 2.5 1 2 2.5 3.5 4.5 4.5.5-1 1.5-1.5 2.5-1l3 2c1 1 1 2 0 3-3 3-7 1-10-2S1 6 4 3z" fill="#fff"/></svg>
    Call Us Today
  </span>
  <span class="hero-arrow" style="left:0">‹</span>
  <span class="hero-arrow" style="right:0">›</span>
</section>

<section class="section about">
  <h2 class="heading">ABOUT <span>BrightHarbor.com</span></h2>
  <p class="lead">We believe that honesty and integrity come before personal profits. We are a family owned and operated company. Our parents raised us to take care of each other and that's exactly what we've done. We treat each of our clients with the same loyalty and respect that we give each other.<br>We are not looking to have hundreds and hundreds of clients. We are looking to expand our family with a handful of like-minded individuals. Companies who take pride in their work and their customers. We want to build mutually beneficial, lucrative, and long term partnerships.</p>
  <div class="video-frame">
    <div class="video-screen">
      <div class="video-title"><i></i>BrightHarbor Web Design</div>
    </div>
    <svg style="position:absolute;left:219px;top:119px" width="72" height="72" viewBox="0 0 72 72"><circle cx="36" cy="36" r="32" fill="rgba(40,40,40,.75)" stroke="#fff" stroke-width="3"/><path d="M29 22l22 14-22 14z" fill="#fff"/></svg>
  </div>
  <div class="video-stand"></div>
  <span class="btn about-cta">
    <svg width="20" height="20" viewBox="0 0 20 20"><path d="M4 3c1-1 2-1 3 0l2 3c.5 1 0 2-1 2.5 1 2 2.5 3.5 4.5 4.5.5-1 1.5-1.5 2.5-1l3 2c1 1 1 2 0 3-3 3-7 1-10-2S1 6 4 3z" fill="#fff"/></svg>
    Call Us Today
  </span>
</section>

<section class="section services" aria-label="Services we provide">
  <svg class="services-art" width="1200" height="758" viewBox="0 0 1200 758" aria-hidden="true">
    <path d="M0 0h1200v22c-120-18-240 10-360-2s-240-20-360 0-240 10-480-6z" fill="#ffffff"/>
    <circle cx="600" cy="410" r="190" fill="none" stroke="#ffffff" stroke-opacity=".35" stroke-width="2" stroke-dasharray="4 6"/>
    <circle cx="600" cy="410" r="74" fill="#ffffff" opacity=".08"/>
    <circle cx="600" cy="410" r="58" fill="#ffffff"/>
    <text x="600" y="415" text-anchor="middle" font-family="Open Sans,Arial,sans-serif" font-size="14" font-weight="700" fill="#1e2b31">BrightHarbor</text>

    <g>
      <circle cx="530" cy="232" r="32" fill="#f7941d"/>
      <circle cx="654" cy="228" r="32" fill="#29a9e0"/>
      <circle cx="752" cy="300" r="32" fill="#8cc63f"/>
      <circle cx="784" cy="420" r="32" fill="#8e44ad"/>
      <circle cx="732" cy="535" r="32" fill="#e8501e"/>
      <circle cx="620" cy="598" r="32" fill="#1e88c7"/>
      <circle cx="490" cy="568" r="32" fill="#17a2b8"/>
      <circle cx="420" cy="464" r="32" fill="#c5d62a"/>
      <circle cx="430" cy="336" r="32" fill="#1ba39c"/>
    </g>

    <g fill="none" stroke="#fff" stroke-width="2.5" stroke-linecap="round" stroke-linejoin="round">
      <path d="M518 226h24v14h-14l-6 5v-5h-4z"/>
      <rect x="641" y="217" width="26" height="17" rx="2"/><path d="M648 240h12M654 234v6"/>
      <path d="M742 312l12-24 6 6-12 24zM742 312l-2 4"/>
      <rect x="775" y="406" width="18" height="28" rx="3"/><path d="M782 429h4"/>
      <path d="M732 524a9 9 0 0 1 9 9c0 7-9 14-9 14s-9-7-9-14a9 9 0 0 1 9-9z"/><circle cx="732" cy="533" r="3"/>
      <circle cx="617" cy="595" r="9"/><path d="M624 602l8 8"/>
      <circle cx="490" cy="568" r="7"/><path d="M490 553v5M490 578v5M475 568h5M500 568h5M480 558l3 3M497 575l3 3M480 578l3-3M497 561l3-3"/>
      <rect x="406" y="452" width="28" height="20" rx="2"/><path d="M411 466l7-7 5 4 6-6"/>
      <rect x="420" y="322" width="20" height="28" rx="2"/><path d="M425 330h10M425 336h10M425 342h6"/>
    </g>

    <g font-family="Open Sans,Arial,sans-serif" font-size="12" font-weight="700" fill="#fff" text-anchor="middle">
      <circle cx="562" cy="214" r="12" fill="#f7941d" stroke="#fff" stroke-width="2"/><text x="562" y="218">9</text>
      <circle cx="690" cy="206" r="12" fill="#29a9e0" stroke="#fff" stroke-width="2"/><text x="690" y="210">1</text>
      <circle cx="790" cy="316" r="12" fill="#8cc63f" stroke="#fff" stroke-width="2"/><text x="790" y="320">2</text>
      <circle cx="790" cy="464" r="12" fill="#8e44ad" stroke="#fff" stroke-width="2"/><text x="790" y="468">3</text>
      <circle cx="770" cy="518" r="12" fill="#e8501e" stroke="#fff" stroke-width="2"/><text x="770" y="522">4</text>
      <circle cx="652" cy="576" r="12" fill="#1e88c7" stroke="#fff" stroke-width="2"/><text x="652" y="580">5</text>
      <circle cx="522" cy="590" r="12" fill="#17a2b8" stroke="#fff" stroke-width="2"/><text x="522" y="594">6</text>
      <circle cx="440" cy="500" r="12" fill="#c5d62a" stroke="#fff" stroke-width="2"/><text x="440" y="504">7</text>
      <circle cx="398" cy="356" r="12" fill="#1ba39c" stroke="#fff" stroke-width="2"/><text x="398" y="360">8</text>
    </g>

    <g font-family="Open Sans,Arial,sans-serif" font-size="12" font-weight="700">
      <text x="340" y="186" fill="#f7941d">Consulting Service</text>
      <text x="700" y="168" fill="#29a9e0">Website Design &amp; Management</text>
      <text x="800" y="272" fill="#8cc63f">Logo Design &amp; Branding Materials</text>
      <text x="830" y="398" fill="#8e44ad">Application Design &amp;</text>
      <text x="830" y="412" fill="#8e44ad">Development</text>
      <text x="794" y="520" fill="#e8501e">Local Seo Management</text>
      <text x="664" y="640" fill="#1e88c7">Search Engine Optimization</text>
      <text x="250" y="574" fill="#8cc63f">Social Media Marketing</text>
      <text x="130" y="446" fill="#f7941d">Marketing Material &amp; Print Design</text>
      <text x="196" y="298" fill="#29a9e0">Outsourcing Management</text>
    </g>
    <g font-family="Open Sans,Arial,sans-serif" font-size="10" fill="#d5dadd">
      <text x="340" y="202">Quick audit and clear</text><text x="340" y="215">advice for your</text><text x="340" y="228">business goals.</text>
      <text x="700" y="184">Fast custom sites built</text><text x="700" y="197">and kept up to date.</text>
      <text x="812" y="288">Logos, cards and</text><text x="812" y="301">brand kits made</text><text x="812" y="314">to fit you.</text>
      <text x="830" y="428">Apps that help your</text><text x="830" y="441">customers reach you.</text>
      <text x="794" y="536">Get found by local</text><text x="794" y="549">buyers near you.</text>
      <text x="664" y="656">Climb search results</text><text x="664" y="669">with steady work.</text>
      <text x="250" y="590">Posts and ads that</text><text x="250" y="603">grow your reach.</text>
      <text x="220" y="462">Flyers, signs and</text><text x="220" y="475">print made simple.</text>
      <text x="246" y="314">We handle the tasks</text><text x="246" y="327">you would rather</text><text x="246" y="340">not manage.</text>
    </g>
  </svg>
  <h2 class="heading" style="position:relative">SERVICES WE PROVIDE</h2>
  <p class="lead" style="position:relative">Lorem ipsum dolor sit amet, consectetuer adipiscing elit, sed diam nonummy nibh euismod tincidunt ut laoreet dolore magna aliquam erat volutpat. Ut wisi enim ad minim veniam, quis nostrud exerci.</p>
</section>

<section class="section plans">
  <h2 class="heading">SELECT YOUR PLAN</h2>
  <div class="plans-floor" role="img" aria-label="Wooden floor"></div>

  <div class="plan" style="left:160px">
    <div class="plan-icon"><svg width="26" height="26" viewBox="0 0 26 26"><path d="M5 21l7-7M14 4l8 8-6 2-4-4z" stroke="#1b6fb8" stroke-width="2.5" fill="none"/></svg></div>
    <div class="plan-name">Basic Plan</div>
    <div class="plan-body">
      <div class="plan-from">Starting from</div>
      <div class="plan-price accent"><sup>$</sup>52<small>.95</small></div>
      <ul class="plan-list"><li>Lorem Ipsum Dolar Sipsum</li><li>Lorem Ipsum Dolar</li><li>Lorem Ipsum Dolar Sipsum</li><li>Lorem Ipsum Dolar</li></ul>
      <span class="btn plan-btn accent">Get Started &nbsp;→</span>
      <div class="plan-more">More Information &nbsp;▫</div>
    </div>
  </div>
  <div class="plan raised" style="left:394px">
    <div class="plan-icon"><svg width="26" height="26" viewBox="0 0 26 26"><rect x="3" y="5" width="20" height="14" rx="2" fill="none" stroke="#1b6fb8" stroke-width="2.5"/><path d="M9 23h8" stroke="#1b6fb8" stroke-width="2.5"/></svg></div>
    <div class="plan-name">Standard Plan</div>
    <div class="plan-body">
      <div class="plan-from">Starting from</div>
      <div class="plan-price"><sup>$</sup>114<small>.00</small></div>
      <ul class="plan-list"><li>Lorem Ipsum Dolar Sipsum</li><li>Lorem Ipsum Dolar</li><li>Lorem Ipsum Dolar Sipsum</li><li>Lorem Ipsum Dolar</li></ul>
      <span class="btn plan-btn">Get Started &nbsp;→</span>
      <div class="plan-more">More Information &nbsp;▫</div>
    </div>
  </div>
  <div class="plan" style="left:628px">
    <div class="plan-icon"><svg width="26" height="26" viewBox="0 0 26 26"><circle cx="13" cy="13" r="9" fill="none" stroke="#f08a1c" stroke-width="2.5"/><path d="M13 8v10M10 11h6" stroke="#f08a1c" stroke-width="2"/></svg></div>
    <div class="plan-name">Gold Plan</div>
    <div class="plan-body">
      <div class="plan-from">Starting from</div>
      <div class="plan-price"><sup>$</sup>200<small>.95</small></div>
      <ul class="plan-list"><li>Lorem Ipsum Dolar Sipsum</li><li>Lorem Ipsum Dolar</li><li>Lorem Ipsum Dolar Sipsum</li><li>Lorem Ipsum Dolar</li></ul>
      <span class="btn plan-btn">Get Started &nbsp;→</span>
      <div class="plan-more">More Information &nbsp;▫</div>
    </div>
  </div>
  <div class="plan" style="left:862px">
    <div class="plan-icon"><svg width="26" height="26" viewBox="0 0 26 26"><circle cx="11" cy="11" r="7" fill="none" stroke="#1b6fb8" stroke-width="2.5"/><path d="M16 16l6 6" stroke="#1b6fb8" stroke-width="2.5"/></svg></div>
    <div class="plan-name">Platinum Plan</div>
    <div class="plan-body">
      <div class="plan-from">Starting from</div>
      <div class="plan-price"><sup>$</sup>490<small>.00</small></div>
      <ul class="plan-list"><li>Lorem Ipsum Dolar Sipsum</li><li>Lorem Ipsum Dolar</li><li>Lorem Ipsum Dolar Sipsum</li><li>Lorem Ipsum Dolar</li></ul>
      <span class="btn plan-btn">Get Started &nbsp;→</span>
      <div class="plan-more">More Information &nbsp;▫</div>
    </div>
  </div>
</section>

<section class="section clients">
  <h2 class="heading">OUR CLIENTS</h2>
  <p class="lead">Lorem ipsum dolor sit amet, consectetuer adipiscing elit, sed diam nonummy nibh euismod tincidunt ut laoreet dolore magna aliquam erat volutpat. Ut wisi enim ad minim veniam, quis nostrud exerci.</p>
  <span class="row-arrow" style="left:112px">‹</span>
  <div class="client-row">
    <div class="client"><i></i>Halvern</div>
    <div class="client">Brookline</div>
    <div class="client">Brookline</div>
    <div class="client">Corvane</div>
    <div class="client"><i></i>Halvern</div>
    <div class="client"><i></i>Meridale</div>
    <div class="client">Stonepath</div>
    <div class="client">Stonepath</div>
  </div>
  <span class="row-arrow" style="left:1076px">›</span>
</section>

<section class="section why">
  <svg class="why-art" width="1200" height="535" viewBox="0 0 1200 535" aria-hidden="true">
    <path d="M0 0h1200v18c-150-16-300 8-450-4s-300-14-450 2-200 6-300-8z" fill="#fff"/>
    <path d="M418 240a190 190 0 0 0 364 0" fill="none" stroke="#1b6fb8" stroke-width="2" stroke-dasharray="3 6"/>
    <circle cx="600" cy="180" r="56" fill="#1b6fb8"/>
    <circle cx="600" cy="180" r="44" fill="none" stroke="#fff" stroke-width="3"/>
    <text x="600" y="185" text-anchor="middle" font-family="Open Sans,Arial,sans-serif" font-size="12" font-weight="700" fill="#fff">BrightHarbor</text>
    <circle cx="418" cy="236" r="22" fill="#f08a1c"/>
    <circle cx="490" cy="325" r="22" fill="#1b6fb8"/>
    <circle cx="612" cy="375" r="22" fill="#1b6fb8"/>
    <circle cx="726" cy="325" r="22" fill="#1b6fb8"/>
    <circle cx="797" cy="236" r="22" fill="#1b6fb8"/>
    <g stroke="#fff" stroke-width="2.5" fill="none" stroke-linecap="round">
      <path d="M409 236l6 6 12-12"/><rect x="480" y="318" width="20" height="14" rx="2"/><circle cx="612" cy="375" r="9"/><path d="M612 370v5l3 3"/><path d="M717 333c0-7 18-7 18 0"/><circle cx="726" cy="320" r="4"/><rect x="787" y="229" width="20" height="14" rx="2"/><path d="M787 234h20"/>
    </g>
    <g font-family="Open Sans,Arial,sans-serif">
      <text x="388" y="230" text-anchor="end" font-size="13" font-weight="700" fill="#f08a1c">100% Risk Free Investment</text>
      <text x="388" y="248" text-anchor="end" font-size="11" fill="#555b63">Lorem ipsum dolor sit amet, consectetuer</text>
      <text x="388" y="262" text-anchor="end" font-size="11" fill="#555b63">adipiscing elit, sed diam.</text>
      <text x="460" y="320" text-anchor="end" font-size="13" font-weight="700" fill="#1b6fb8">Customer Loyalty Program</text>
      <text x="460" y="338" text-anchor="end" font-size="11" fill="#555b63">Lorem ipsum dolor sit amet, consectetuer</text>
      <text x="460" y="352" text-anchor="end" font-size="11" fill="#555b63">adipiscing elit, sed diam.</text>
      <text x="612" y="418" text-anchor="middle" font-size="13" font-weight="700" fill="#1b6fb8">24/7 U.S. Based Customer Support</text>
      <text x="612" y="436" text-anchor="middle" font-size="11" fill="#555b63">Lorem ipsum dolor sit amet, consectetuer adipiscing</text>
      <text x="612" y="450" text-anchor="middle" font-size="11" fill="#555b63">elit, sed diam.</text>
      <text x="756" y="320" font-size="13" font-weight="700" fill="#1b6fb8">Unmatched Personal Service</text>
      <text x="756" y="338" font-size="11" fill="#555b63">Lorem ipsum dolor sit amet, consectetuer</text>
      <text x="756" y="352" font-size="11" fill="#555b63">adipiscing elit, sed diam.</text>
      <text x="830" y="222" font-size="13" font-weight="700" fill="#1b6fb8">Multiple Payment Options Available</text>
      <text x="830" y="240" font-size="11" fill="#555b63">Lorem ipsum dolor sit amet, consectetuer</text>
      <text x="830" y="254" font-size="11" fill="#555b63">adipiscing elit, sed diam.</text>
    </g>
  </svg>
  <h2 class="heading" style="position:relative">WHY CHOOSE US</h2>
  <p class="lead" style="position:relative">Lorem ipsum dolor sit amet, consectetuer adipiscing elit, sed diam nonummy nibh euismod tincidunt ut laoreet dolore magna aliquam erat volutpat. Ut wisi enim ad minim veniam, quis nostrud exerci.</p>
</section>

<section class="section team">
  <h2 class="heading">OUR TEAM</h2>
  <p class="lead">Lorem ipsum dolor sit amet, consectetuer adipiscing elit, sed diam nonummy nibh euismod tincidunt ut laoreet dolore magna aliquam erat volutpat. Ut wisi enim ad minim veniam, quis nostrud exerci.</p>
  <span class="row-arrow" style="left:112px;top:200px">‹</span>
  <article class="member" style="left:163px">
    <div class="member-photo" role="img" aria-label="Portrait of the chief executive officer"></div>
    <div class="member-name">DANIEL CORWIN</div>
    <div class="member-role">Chief Executive Officer</div>
    <p class="member-bio">Lorem ipsum dolor sit amet, consectetuer adipiscing elit, sed diam nonummy nibh euismod tincidunt ut laoreet dolore magna aliquam erat volutpat... [+]</p>
  </article>
  <article class="member" style="left:640px">
    <div class="member-photo" role="img" aria-label="Portrait of the chief operations officer"></div>
    <div class="member-name">OWEN PRATT</div>
    <div class="member-role">Chief Operations Officer</div>
    <p class="member-bio">Lorem ipsum dolor sit amet, consectetuer adipiscing elit, sed diam nonummy nibh euismod tincidunt ut laoreet dolore magna aliquam erat volutpat... [+]</p>
  </article>
  <span class="row-arrow" style="left:1074px;top:200px">›</span>
</section>

<section class="section inquiry">
  <div class="inquiry-photo" role="img" aria-label="Hands typing on a laptop beside a coffee mug"></div>
  <h2 class="heading">QUICK INQUIRY</h2>
  <div class="field" style="left:490px;top:110px">First Name</div>
  <div class="field" style="left:765px;top:110px">Last Name</div>
  <div class="field" style="left:490px;top:160px">Email</div>
  <div class="field" style="left:765px;top:160px">Phone Number</div>
  <div class="field" style="left:490px;top:210px;border:none">Details About Your Enquiry</div>
  <div class="field box" style="left:490px;top:240px"></div>
  <span class="btn submit">SUBMIT</span>
</section>

<footer class="section site-footer" role="img" aria-label="Dark city skyline behind footer">
  <div class="foot-col" style="left:150px">
    <h4>Quick <span>Links</span></h4>
    <ul><li>Home</li><li>Services</li><li>Pricing</li><li>Our Team</li><li>Success Stories</li><li>Clients</li><li>Contact Us</li></ul>
  </div>
  <div class="foot-col" style="left:342px">
    <h4>Contact <span>Details</span></h4>
    <div><b>BrightHarbor.com</b></div>
    <div>Street Name, City Name</div>
    <div>State Zipcode</div>
    <div>☎ 555-014-2290</div>
    <div>☎ 555-014-2291</div>
    <div>✉ hello@brightharbor.com</div>
  </div>
  <div class="foot-col" style="left:615px">
    <h4>Newsletter <span>Signup</span></h4>
    <div>Lorem ipsum dolor sit amet, consectetuer<br>adipiscing elit, sed diam.</div>
    <div class="foot-input">Email</div>
    <span class="btn foot-btn">Subscribe</span>
  </div>
  <div class="foot-mark"></div>
</footer>

<div class="section copyright">
  <span style="position:absolute;left:150px">Copyright © 2017 BrightHarbor.com. All rights reserved.</span>
  <span style="position:absolute;right:150px">Terms of Use | Privacy Policy</span>
</div>

</body>
</html>
```